Zestora - Landing Page

Need a landing page for a journal app. The app is based on a retrospective board, where each journal entry is split into 3 sections: "What went well", "What Didn't Go Well" and "Things To Try".
The landing page should match the style of all modern web application landing pages. Think Brint, Tivalo, Mirvane. I've included screenshots of the app.
One feature that I want to highlight that is not ready yet, is an AI coach. It will offer insights based on the history of the user's journal entries
1 page

```html
<!DOCTYPE html>
<html lang="en">
<head>
<meta charset="utf-8">
<title>Zestora – Journal App</title>
<link href="https://fonts.googleapis.com/css2?family=Quicksand:wght@600;700&family=Roboto:wght@400;500;700&display=swap" rel="stylesheet">
<style>
:root{
  --blue:#0a55b0;
  --blue-2:#0d72c4;
  --blue-dark:#0647a0;
  --ink:#111418;
  --text:#6f7780;
  --pale:#eef5fc;
  --soft:#f6f7f8;
  --white:#ffffff;
}
*{box-sizing:border-box;margin:0;padding:0}
html,body{width:1200px;height:4360px;overflow:hidden}
body{position:relative;background:var(--white);font-family:'Roboto',sans-serif;color:var(--ink)}
.abs{position:absolute}
.brand{font-family:'Quicksand',sans-serif;font-weight:700;color:var(--ink)}
.site-header{left:0;top:0;width:1200px;height:80px;background:var(--white)}
.site-header .brand{left:110px;top:22px;font-size:26px}
.main-nav{top:29px;left:587px;font-size:13px;font-weight:700}
.main-nav a{position:absolute;color:var(--ink);text-decoration:none;white-space:nowrap}
.main-nav a.active{color:var(--blue);text-decoration:underline;text-underline-offset:4px}
.btn{display:inline-flex;align-items:center;justify-content:center;gap:6px;border-radius:24px;font-weight:700;font-size:13px;text-transform:uppercase;text-decoration:none;white-space:nowrap}
.btn .arr{width:12px;height:12px}
.btn-solid{background:linear-gradient(90deg,var(--blue-dark),var(--blue-2));color:var(--white)}
.btn-ghost{border:2px solid var(--white);color:var(--white)}
.signup{left:967px;top:16px;width:120px;height:42px}
.hero-band{left:0;top:80px;width:1200px;height:720px;background:linear-gradient(120deg,var(--blue-dark),var(--blue-2));clip-path:polygon(0 0,100% 0,100% 445px,0 720px)}
.pale-band{left:0;top:80px;width:1200px;height:1245px;background:linear-gradient(180deg,#f4f8fd,var(--pale))}
.soft-band{left:0;top:1795px;width:1200px;height:600px;background:var(--soft)}
.coach-band{left:0;top:2192px;width:1200px;height:644px;background:linear-gradient(120deg,var(--blue-dark),var(--blue-2));clip-path:polygon(0 195px,100% 0,100% 100%,0 100%)}
.connect-band{left:0;top:3620px;width:1200px;height:367px;background:linear-gradient(120deg,var(--blue-dark),var(--blue-2))}
.center{left:0;width:1200px;text-align:center}
.h-hero{top:168px;font-family:'Quicksand',sans-serif;font-weight:700;font-size:38px;letter-spacing:1px;color:var(--white)}
.lead{font-size:15px;line-height:27px;color:var(--white)}
.h-sec{font-family:'Quicksand',sans-serif;font-weight:700;font-size:29px;letter-spacing:.5px}
.h-white{color:var(--white)}
.rule{height:4px;width:80px;background:var(--blue)}
.rule-white{background:var(--white)}
.body{font-size:15.5px;line-height:28.4px;color:var(--text);width:395px}
.mockup{border-radius:14px;background:linear-gradient(180deg,#eef0f3,#d9dce1);box-shadow:0 30px 30px -22px rgba(0,0,0,.25)}
.portrait{left:653px;top:3107px;width:425px;height:425px;border-radius:50%;background:radial-gradient(circle at 55% 40%,#8c96a0,#3f5360 55%,#cfd4d8 100%)}
.play{left:829px;top:3282px;width:72px;height:72px}
.hr{left:95px;width:1010px;height:1px;background:#dde4ee}
.foot-nav a{position:absolute;font-size:13px;font-weight:700;color:var(--ink);text-decoration:none;white-space:nowrap}
.email{left:322px;top:4145px;width:555px;height:50px;border:1px solid #cfd6e2;border-radius:25px;font-size:12px;letter-spacing:5px;color:#555;padding:17px 28px}
.send{left:836px;top:4153px;width:34px;height:34px}
.social{width:42px;height:42px;border-radius:50%;background:#0b0c0e}
.copy{top:4313px;font-size:13px;color:#222}
</style>
</head>
<body>

<div class="abs pale-band"></div>
<div class="abs hero-band"></div>

<header class="abs site-header">
  <div class="abs brand">Zestora</div>
  <nav class="abs main-nav">
    <a style="left:0">FEATURES</a>
    <a class="active" style="left:104px">PRICING</a>
    <a style="left:188px">ABOUT</a>
    <a style="left:260px">CONTACT US</a>
  </nav>
  <a class="abs btn btn-solid signup">
    <svg class="arr" viewBox="0 0 12 12"><circle cx="6" cy="3.5" r="2.5" fill="#fff"/><path d="M1 11c0-3 2-4.5 5-4.5s5 1.5 5 4.5z" fill="#fff"/></svg>Sign up</a>
</header>

<h1 class="abs center h-hero">REFLECT - IMPROVE - THRIVE</h1>
<p class="abs center lead" style="top:228px">Organize your thoughts with Zestora, a journal app that helps you reflect on your<br>day using a simple retrospective board.</p>
<div class="abs center" style="top:313px"><a class="btn btn-ghost" style="width:166px;height:44px">Get started
  <svg class="arr" viewBox="0 0 12 12"><circle cx="6" cy="6" r="6" fill="#fff"/><path d="M5 3.5 7.5 6 5 8.5" stroke="#0a55b0" stroke-width="1.6" fill="none"/></svg></a></div>
<div class="abs mockup" style="left:322px;top:411px;width:565px;height:347px" role="img" aria-label="Laptop showing the journal entry board with three columns"></div>

<div class="abs mockup" style="left:130px;top:945px;width:483px;height:270px" role="img" aria-label="Laptop showing a list of past journal entries"></div>
<h2 class="abs h-sec" style="left:677px;top:928px">WHAT WENT WELL</h2>
<div class="abs rule" style="left:677px;top:976px"></div>
<p class="abs body" style="left:677px;top:1003px">Lorem ipsum dolor sit amet, consectetur adipiscing elit, sed do eiusmod tempor incididunt ut labore et dolore magna aliqua. Ut enim ad minim veniam, quis nostrud exercitation ullamco laboris nisi ut aliquip ex ea commodo consequat. Duis aute irure dolor in reprehenderit in voluptate velit esse</p>
<a class="abs btn btn-solid" style="left:678px;top:1199px;width:163px;height:44px">Learn more
  <svg class="arr" viewBox="0 0 12 12"><circle cx="6" cy="6" r="6" fill="#fff"/><path d="M5 3.5 7.5 6 5 8.5" stroke="#0a55b0" stroke-width="1.6" fill="none"/></svg></a>

<h2 class="abs h-sec" style="left:161px;top:1418px">WHAT DIDN'T GO WELL</h2>
<div class="abs rule" style="left:161px;top:1466px"></div>
<p class="abs body" style="left:161px;top:1491px">Lorem ipsum dolor sit amet, consectetur adipiscing elit, sed do eiusmod tempor incididunt ut labore et dolore magna aliqua. Ut enim ad minim veniam, quis nostrud exercitation ullamco laboris nisi ut aliquip ex ea commodo consequat. Duis aute irure dolor in reprehenderit in voluptate velit esse</p>
<a class="abs btn btn-solid" style="left:162px;top:1688px;width:163px;height:44px">Learn more
  <svg class="arr" viewBox="0 0 12 12"><circle cx="6" cy="6" r="6" fill="#fff"/><path d="M5 3.5 7.5 6 5 8.5" stroke="#0a55b0" stroke-width="1.6" fill="none"/></svg></a>
<div class="abs mockup" style="left:596px;top:1419px;width:479px;height:270px" role="img" aria-label="Laptop showing a filled-in journal entry"></div>

<div class="abs soft-band"></div>
<div class="abs coach-band"></div>
<div class="abs mockup" style="left:130px;top:1879px;width:483px;height:270px" role="img" aria-label="Laptop showing an empty journal entry board"></div>
<h2 class="abs h-sec" style="left:677px;top:1863px">THINGS TO TRY</h2>
<div class="abs rule" style="left:677px;top:1911px"></div>
<p class="abs body" style="left:677px;top:1937px">Lorem ipsum dolor sit amet, consectetur adipiscing elit, sed do eiusmod tempor incididunt ut labore et dolore magna aliqua. Ut enim ad minim veniam, quis nostrud exercitation ullamco laboris nisi ut aliquip ex ea commodo consequat. Duis aute irure dolor in reprehenderit in voluptate velit esse</p>
<a class="abs btn btn-solid" style="left:678px;top:2133px;width:163px;height:44px">Learn more
  <svg class="arr" viewBox="0 0 12 12"><circle cx="6" cy="6" r="6" fill="#fff"/><path d="M5 3.5 7.5 6 5 8.5" stroke="#0a55b0" stroke-width="1.6" fill="none"/></svg></a>

<h2 class="abs center h-sec h-white" style="top:2367px">AI COACH</h2>
<p class="abs center lead" style="top:2435px">Lorem ipsum dolor sit amet, consectetur adipiscing elit, sed do eiusmod tempor incididunt<br>ut labore et dolore magna aliqua. Ut enim ad minim veniam, quis</p>
<div class="abs center" style="top:2514px"><a class="btn btn-ghost" style="width:166px;height:44px">Learn more
  <svg class="arr" viewBox="0 0 12 12"><circle cx="6" cy="6" r="6" fill="#fff"/><path d="M5 3.5 7.5 6 5 8.5" stroke="#0a55b0" stroke-width="1.6" fill="none"/></svg></a></div>
<div class="abs mockup" style="left:322px;top:2607px;width:565px;height:347px" role="img" aria-label="Laptop showing the journal entry board"></div>

<h2 class="abs h-sec" style="left:161px;top:3159px">TESTIMONIAL</h2>
<div class="abs rule" style="left:161px;top:3206px"></div>
<p class="abs body" style="left:161px;top:3231px">Lorem ipsum dolor sit amet, consectetur adipiscing elit, sed do eiusmod tempor incididunt ut labore et dolore magna aliqua. Ut enim ad minim veniam, quis nostrud exercitation ullamco laboris nisi ut aliquip ex ea commodo consequat. Duis aute irure dolor in reprehenderit in voluptate velit esse</p>
<a class="abs btn btn-solid" style="left:162px;top:3427px;width:163px;height:44px">Learn more
  <svg class="arr" viewBox="0 0 12 12"><circle cx="6" cy="6" r="6" fill="#fff"/><path d="M5 3.5 7.5 6 5 8.5" stroke="#0a55b0" stroke-width="1.6" fill="none"/></svg></a>
<div class="abs portrait" role="img" aria-label="Photo of a customer seated by a bright office window"></div>
<svg class="abs play" viewBox="0 0 72 72" aria-label="Play video"><circle cx="36" cy="36" r="36" fill="#fff"/><path d="M29 24 49 36 29 48z" fill="#111"/></svg>

<div class="abs connect-band"></div>
<h2 class="abs center h-sec h-white" style="top:3700px">GET CONNECTED</h2>
<div class="abs rule rule-white" style="left:560px;top:3746px"></div>
<p class="abs center lead" style="top:3768px">Lorem ipsum dolor sit amet, consectetur adipiscing elit, sed do eiusmod tempor incididunt<br>ut labore et dolore magna aliqua. Ut enim ad minim veniam, quis</p>
<div class="abs center" style="top:3862px"><a class="btn btn-ghost" style="width:166px;height:44px">Get started
  <svg class="arr" viewBox="0 0 12 12"><circle cx="6" cy="6" r="6" fill="#fff"/><path d="M5 3.5 7.5 6 5 8.5" stroke="#0a55b0" stroke-width="1.6" fill="none"/></svg></a></div>

<div class="abs hr" style="top:4009px"></div>
<div class="abs center brand" style="top:4049px;font-size:25px">Zestora</div>
<nav class="foot-nav">
  <a style="left:428px;top:4101px">FEATURES</a>
  <a style="left:532px;top:4101px">PRICING</a>
  <a style="left:616px;top:4101px">ABOUT</a>
  <a style="left:688px;top:4101px">CONTACT US</a>
</nav>
<div class="abs email">ENTER EMAIL ADDRESS</div>
<svg class="abs send" viewBox="0 0 34 34"><circle cx="17" cy="17" r="17" fill="#0a55b0"/><path d="M13 12l5 5-5 5M17 12l5 5-5 5" stroke="#fff" stroke-width="1.8" fill="none"/></svg>
<div class="abs social" style="left:531px;top:4225px" aria-label="Social link"></div>
<div class="abs social" style="left:579px;top:4225px;background:var(--blue)" aria-label="Social link"></div>
<div class="abs social" style="left:626px;top:4225px" aria-label="Social link"></div>
<div class="abs hr" style="top:4292px"></div>
<p class="abs center copy">Copyright@2024. All Rights Reserved By Zestora</p>

</body>
</html>
```